Create the design of Sitelaunch (in photoshop or similar)

*edit* What we wanna see is a sketch of a first page, and then in the end 5 page designs, but the main page will be the big tasks other pages are just basically pop-ups or form. *edit*

We need a web design for our new startup Sitelaunch in turn will be providing web pages to smaller business. So the purpose of the page is to clearly showcase the message in a web 3.0 fashion, good design looks but function should always be the main focus.Further more we are looking for a long term relationship with a good designer / design company that can help us design the future web sites for our customers as well.

We need you to understand web, not just design. You need to be up to date with how web looks and works, and how to make it as simple and easy to use as possible for the customer and at the same time good looking.

Colors and layout are free to choose, but we really like the kind of layout that forkcomet.com has so feel free to be inspired by them.

We want all of the pages design, but the main/landing page will be the big part, the rest are small pages that will use the same design frame as the main page.

PS. We just want the design in photoshop or illustrator format, the website will then be built in word press by word press experts (let us know if you/company also possess this knowledge)

Target Market(s)

Small to medium sized business, mostly owner/entrepreneur driven companies.

Industry/Entity Type

Business

Font styles to use
Other font styles liked:
• Helvetica for the win

Requirements
Must have
• Great and simple design, a child should be able to understand the message and also enjoy reading it. Should be a funny website while still being professional, i.e. see postbadger.com for example.

```html
<!DOCTYPE html>
<html lang="en">
<head>
<meta charset="utf-8">
<title>Sitelaunch – Most Convenient Web Ever</title>
<link rel="stylesheet" href="https://fonts.googleapis.com/css2?family=Arimo:wght@400;700&family=Lato:wght@300;700&display=swap">
<style>
  :root {
    --brand: #3f58c8;
    --brand-dark: #2f47ad;
    --brand-field: #2d43a3;
    --ink: #444a52;
    --ink-soft: #8a8f96;
    --line: #b9bcc0;
    --white: #ffffff;
    --hero-top: #1d2a4a;
    --hero-bottom: #0f1526;
    --gold-top: #d9c531;
    --gold-bottom: #b8a218;
    --chat: #4a4d52;
    --tunewave: #7dbe1f;
    --device: #f4f5f7;
  }
  * { box-sizing: border-box; margin: 0; padding: 0; }
  html, body { width: 1200px; height: 2350px; overflow: hidden; }
  body { position: relative; background: var(--white); font-family: "Arimo", Helvetica, Arial, sans-serif; color: var(--ink); }
  .abs { position: absolute; }

  /* header */
  .topbar { left: 0; top: 0; width: 1200px; height: 69px; background: var(--brand); }
  .brand-mark { left: 100px; top: 12px; width: 44px; height: 44px; border: 2px solid var(--white); border-radius: 50%; }
  .brand-name { left: 152px; top: 14px; color: var(--white); font-weight: 700; font-size: 19px; line-height: 22px; }
  .brand-tag { left: 153px; top: 37px; color: var(--white); font-size: 12px; }
  .nav-link { top: 27px; color: var(--white); font-size: 12.5px; white-space: nowrap; text-decoration: none; }
  .nav-pill { top: 22px; border: 1.5px solid var(--white); border-radius: 14px; padding: 4px 12px; }

  .subbar { left: 0; top: 69px; width: 1200px; height: 47px; background: var(--white); border-bottom: 1px solid #e4e4e4; }
  .perk { top: 86px; font-size: 12.5px; color: var(--ink-soft); display: flex; align-items: center; gap: 6px; white-space: nowrap; }
  .perk i { width: 11px; height: 11px; border-radius: 50%; border: 1.5px solid var(--ink-soft); display: inline-block; }
  .lang { left: 760px; top: 85px; font-size: 11.5px; color: var(--ink-soft); display: flex; align-items: center; gap: 6px; }
  .lang b { width: 14px; height: 10px; background: #c9d1ee; display: inline-block; }
  .search { left: 874px; top: 79px; width: 198px; height: 28px; border: 1px solid #d6d6d6; font-size: 12px; color: var(--ink-soft); padding: 6px 10px; }
  .search-btn { left: 1072px; top: 79px; width: 28px; height: 28px; background: var(--brand); }

  /* hero */
  .hero { left: 0; top: 116px; width: 1200px; height: 536px; background: radial-gradient(ellipse at 35% 40%, #3a4c78 0%, var(--hero-top) 45%, var(--hero-bottom) 100%); }
  .hero-title { left: 0; width: 762px; top: 250px; text-align: center; font-family: "Lato", Helvetica, sans-serif; font-weight: 300; font-size: 47px; color: var(--white); }
  .hero-title strong { font-weight: 700; }
  .hero-sub { left: 0; width: 762px; top: 322px; text-align: center; font-size: 20px; line-height: 27px; color: var(--white); }
  .hero-news { left: 0; width: 762px; top: 415px; text-align: center; font-size: 20px; color: var(--white); }
  .hero-input { left: 125px; top: 467px; width: 350px; height: 36px; background: var(--white); border: 1px solid #ccc; font-size: 15px; color: #aaa; padding: 9px 12px; }
  .hero-btn { left: 490px; top: 467px; width: 149px; height: 36px; background: var(--brand); border: 1px solid #6d84e0; color: var(--white); font-size: 17px; text-align: center; line-height: 34px; }
  .hero-arrow { top: 364px; width: 40px; height: 40px; border: 2px solid var(--white); border-radius: 50%; }
  .device { left: 714px; top: 180px; width: 333px; height: 494px; border-radius: 22px; background: linear-gradient(160deg, #ffffff 0%, #e6e8ec 100%); box-shadow: 0 10px 30px rgba(0,0,0,.18); }
  .device-cam { left: 879px; top: 203px; width: 5px; height: 5px; border-radius: 50%; background: #333; }
  .device-screen { left: 730px; top: 227px; width: 300px; height: 397px; border: 3px solid #1c1f26; background: linear-gradient(#2d3f86 0%, #1b2440 32%, #f6f6f6 34%, #eceef2 80%, #7dbe1f 80%, #7dbe1f 100%); }
  .device-home { left: 869px; top: 640px; width: 22px; height: 22px; border-radius: 50%; border: 1.5px solid #d0d2d6; }
  .dots { left: 588px; top: 667px; display: flex; gap: 5px; }
  .dots span { width: 6px; height: 6px; border-radius: 50%; background: #c2c2c2; }
  .dots span:first-child { background: var(--brand); }

  /* sections */
  .icon-ring { width: 120px; height: 120px; border: 1.5px solid #555; border-radius: 50%; }
  .icon-fill { width: 76px; height: 76px; border-radius: 50%; background: #e9eaec; margin: 21px; }
  .section-title { font-size: 22px; font-weight: 400; color: var(--ink); text-align: center; }
  .rule { height: 1px; background: var(--line); }
  .bullets { left: 0; width: 1200px; top: 892px; font-size: 17px; text-align: center; line-height: 27px; }
  .bullets li { list-style: none; }
  .bullets li::before { content: ""; display: inline-block; width: 9px; height: 9px; border-radius: 50%; background: #c4c4c4; margin-right: 18px; vertical-align: 2px; }
  .col-text { font-size: 17px; line-height: 26px; text-align: center; }
  .photo { top: 1266px; height: 266px; }
  .tunewave { left: 614px; top: 1266px; width: 486px; height: 266px; background: var(--tunewave); color: var(--white); font-weight: 700; font-size: 62px; text-align: center; line-height: 266px; }
  .btn-blue { background: var(--brand); color: var(--white); font-size: 14px; text-align: center; border-bottom: 2px solid var(--brand-dark); }

  /* calculator */
  .calc { left: 100px; top: 1756px; width: 1003px; height: 328px; background: var(--brand); box-shadow: 3px 3px 0 var(--brand-dark); }
  .calc-label { left: 132px; font-size: 17px; color: var(--white); }
  .calc-field { left: 401px; width: 158px; height: 34px; background: var(--brand-field); color: var(--white); font-size: 17px; padding: 7px 12px; }
  .calc-note { left: 580px; width: 505px; font-size: 11.5px; line-height: 14px; color: var(--white); }
  .cta-gold { left: 276px; top: 2121px; width: 664px; height: 65px; background: linear-gradient(var(--gold-top), var(--gold-bottom)); color: #3b3a1e; font-size: 16px; text-align: center; line-height: 65px; border: 1px solid #a79418; }

  /* footer */
  .chat { left: 877px; top: 2209px; width: 224px; height: 43px; background: var(--chat); color: var(--white); font-size: 15px; padding: 12px 20px; }
  .footer { left: 0; top: 2252px; width: 1200px; height: 98px; background: var(--brand); }
  .foot-nav { left: 0; width: 1200px; top: 2268px; text-align: center; font-size: 12.5px; color: var(--white); }
  .foot-nav span { margin: 0 12px; }
  .foot-brand { top: 2310px; color: var(--white); font-size: 17px; line-height: 18px; }
  .foot-brand small { display: block; font-size: 11px; }
  .foot-copy { left: 0; width: 1200px; top: 2319px; text-align: center; font-size: 12.5px; color: var(--white); }
  .foot-pay { top: 2320px; font-size: 12px; font-weight: 700; color: var(--white); white-space: nowrap; }
  .to-top { left: 1128px; top: 2283px; width: 36px; height: 36px; border: 1.5px solid var(--white); }
</style>
</head>
<body>

<!-- header -->
<div class="abs topbar"></div>
<div class="abs brand-mark"></div>
<div class="abs brand-name">Sitelaunch</div>
<div class="abs brand-tag">Most convenient web ever</div>
<svg class="abs" style="left:409px;top:27px" width="14" height="13" viewBox="0 0 14 13"><path d="M7 0 L14 6 H12 V13 H8.5 V9 H5.5 V13 H2 V6 H0 Z" fill="#fff"/></svg>
<a class="abs nav-link nav-pill" style="left:436px">How it works</a>
<a class="abs nav-link" style="left:555px">About us</a>
<a class="abs nav-link" style="left:641px">Contact us</a>
<a class="abs nav-link" style="left:740px">FAQ</a>
<a class="abs nav-link" style="left:802px">Privacy Policy</a>
<a class="abs nav-link" style="left:920px">What people think?</a>
<a class="abs nav-link" style="left:1067px">Order</a>

<div class="abs subbar"></div>
<div class="abs perk" style="left:100px"><i></i>Free unlimited support</div>
<div class="abs perk" style="left:293px"><i></i>Free Updates</div>
<div class="abs perk" style="left:426px"><i></i>Need Help?</div>
<div class="abs perk" style="left:547px"><i></i>Afordale Price</div>
<div class="abs lang">Language: <b></b> ▾</div>
<div class="abs search">Search</div>
<div class="abs search-btn">
  <svg width="28" height="28" viewBox="0 0 28 28"><circle cx="12.5" cy="12.5" r="5" fill="none" stroke="#fff" stroke-width="2"/><path d="M16 16 L20 20" stroke="#fff" stroke-width="2.2"/></svg>
</div>

<!-- hero -->
<div class="abs hero" role="img" aria-label="Blurred city lights at night behind the headline"></div>
<h1 class="abs hero-title">Most Convenient <strong>Web Ever</strong></h1>
<p class="abs hero-sub">Your website on subscription autopilot with free unlimited<br>support and updates</p>
<p class="abs hero-news">Signup For Our Newsletter</p>
<div class="abs hero-input">Email address...</div>
<div class="abs hero-btn">Sign Up</div>
<svg class="abs hero-arrow" style="left:30px" viewBox="0 0 40 40"><path d="M23 13 L16 20 L23 27" fill="none" stroke="#fff" stroke-width="2"/></svg>
<svg class="abs hero-arrow" style="left:1131px" viewBox="0 0 40 40"><path d="M17 13 L24 20 L17 27" fill="none" stroke="#fff" stroke-width="2"/></svg>
<div class="abs device"></div>
<div class="abs device-cam"></div>
<div class="abs device-screen" role="img" aria-label="Tablet screen showing a small preview of the Sitelaunch home page"></div>
<div class="abs device-home"></div>
<div class="abs dots"><span></span><span></span><span></span></div>

<!-- what is -->
<div class="abs icon-ring" style="left:540px;top:705px"><div class="icon-fill" role="img" aria-label="Line icon of a rocket beside a question mark"></div></div>
<h2 class="abs section-title" style="left:0;width:1200px;top:830px">What is Sitelaunch?</h2>
<div class="abs rule" style="left:222px;top:870px;width:762px"></div>
<ul class="abs bullets">
  <li>Your website on subscription autopilot with free unlimited support and updates.</li>
  <li>Delivered by professionals.</li>
</ul>

<!-- cost / unhappy -->
<div class="abs icon-ring" style="left:281px;top:1001px" role="img" aria-label="Money bag icon">
  <svg width="117" height="117" viewBox="0 0 120 120"><path d="M54 46 C36 60 36 86 60 86 C84 86 84 60 66 46 M50 36 L70 36 L64 46 L56 46 Z" fill="none" stroke="#555" stroke-width="2"/><text x="53" y="77" font-family="Arimo, sans-serif" font-size="22" fill="#555">$</text></svg>
</div>
<div class="abs icon-ring" style="left:795px;top:1001px"><div class="icon-fill" role="img" aria-label="Unhappy emoticon line icon"></div></div>
<h2 class="abs section-title" style="left:100px;width:470px;top:1125px">What does it cost?</h2>
<h2 class="abs section-title" style="left:614px;width:470px;top:1125px">If you are unhappy?</h2>
<div class="abs rule" style="left:100px;top:1167px;width:470px"></div>
<div class="abs rule" style="left:614px;top:1167px;width:470px"></div>
<p class="abs col-text" style="left:95px;width:490px;top:1192px">About the same as 1 a day and guaranteed less than a really good night out with the gang</p>
<p class="abs col-text" style="left:609px;width:495px;top:1192px">Cancel the same day, we will refund you all your money and buy you a year of Tunewave subscription</p>
<div class="abs photo" style="left:100px;width:234px;background:linear-gradient(#8a6a55,#3c2a20)" role="img" aria-label="Cup of cappuccino with latte art"></div>
<div class="abs photo" style="left:352px;width:234px;background:linear-gradient(135deg,#7a3f8a,#d48a3a 60%,#3a1a40)" role="img" aria-label="Friends dancing at a party"></div>
<div class="abs tunewave">Tunewave</div>
<div class="abs btn-blue" style="left:235px;top:1552px;width:221px;height:30px;line-height:29px">See price details here</div>

<!-- calculator -->
<h2 class="abs section-title" style="left:0;width:1200px;top:1638px">Test your website now!</h2>
<div class="abs rule" style="left:357px;top:1676px;width:467px"></div>
<p class="abs" style="left:0;width:1200px;top:1704px;text-align:center;font-size:17px">How many more customers could you get every month?</p>

<div class="abs calc"></div>
<div class="abs calc-label" style="top:1785px">Visitors per month</div>
<div class="abs calc-field" style="top:1778px">100000</div>
<div class="abs calc-note" style="top:1780px">(If you can't remember, put in 10 000. Number of visitors to yourwebsite monthly.)</div>

<div class="abs calc-label" style="top:1846px">Current conversion rate in %</div>
<div class="abs calc-field" style="top:1839px">15%</div>
<div class="abs calc-note" style="top:1837px">(If you can't remember put in a 1. The percentage of the visitors to your web that ends up doing something interesting, for example buying your product orservice. It is usually 15%)</div>

<div class="abs calc-label" style="top:1907px">Improve conversion rate, 13%</div>
<div class="abs calc-field" style="top:1900px">13%</div>
<div class="abs calc-note" style="top:1898px">(let's aim for 13%,a typical increase is around2%. Better web has a clear purpose, is up to date and easy to understand, that means better conversion.Fill in what your goal is with conversion increase for a new website)</div>

<div class="abs calc-label" style="top:1968px">Average purchase in SEK</div>
<div class="abs calc-field" style="top:1961px;width:75px">100</div>
<div class="abs calc-field" style="left:487px;top:1961px;width:72px;padding-right:4px">SEK <span style="float:right;font-size:10px;line-height:22px">▼</span></div>
<div class="abs calc-note" style="top:1959px">(what is theaverage amount a customer spends with your company within the first year, it can range from 100 100 000+, if you can't remember then guestimate)</div>

<div class="abs btn-blue" style="left:528px;top:2024px;width:180px;height:36px;line-height:35px;font-weight:700;background:var(--brand-field)">CALCULATE</div>

<div class="abs cta-gold">SEE PRICES AND DETAILS FOR "MOST CONVENIENT WEB EVER"</div>

<!-- footer -->
<div class="abs chat">Chat with Us <span style="float:right;font-size:12px">▲</span></div>
<div class="abs footer"></div>
<div class="abs foot-nav"><span>How it works</span>I<span>About us</span>I<span>Contact us</span>I<span>FAQ</span>I<span>Privacy Policy</span>I<span>What people think?</span>I<span>Order</span></div>
<div class="abs brand-mark" style="left:100px;top:2305px;width:38px;height:38px;border-width:1.5px"></div>
<div class="abs foot-brand" style="left:146px">Sitelaunch<small>Most convenient web ever</small></div>
<div class="abs foot-copy">Yoursite © 2014 All Rights Reserved.</div>
<div class="abs foot-pay" style="left:862px">Paysplit</div>
<div class="abs foot-pay" style="left:920px">Cardly</div>
<div class="abs foot-pay" style="left:970px;font-weight:400;font-size:10px;top:2321px">Socialnet · Chirpr · Clipster</div>
<svg class="abs to-top" viewBox="0 0 36 36"><path d="M11 21 L18 14 L25 21" fill="none" stroke="#fff" stroke-width="2"/></svg>

</body>
</html>
```